Redesign of Form/Document Navigation Page

I need a redesign of our document and navigation bar on the left. We want the same navigation bar layout/setup but want the buttons and typography to be simple and matching all over. The form needs to be aesthetically pleasing and fit within the page.

1st attachment is our Direct Deposit and the second is the form continued.

```html
<!DOCTYPE html>
<html lang="en">
<head>
<meta charset="utf-8">
<title>Direct Deposit – Sentinel Watch Services</title>
<link href="https://fonts.googleapis.com/css2?family=Open+Sans:wght@400;600;700&display=swap" rel="stylesheet">
<style>
  :root {
    --brand-blue: #1f5fa8;
    --brand-gold: #f2b321;
    --ink: #333333;
    --ink-soft: #555555;
    --ink-muted: #777777;
    --line: #d6d6d6;
    --panel-bg: #ffffff;
    --row-alt: #f5f5f5;
    --footer-bg: #f4f4f4;
    --scroll-track: #e4e7ea;
    --scroll-thumb: #6b7785;
  }
  * { box-sizing: border-box; margin: 0; padding: 0; }
  html, body { width: 1200px; height: 826px; overflow: hidden; background: #fff; }
  body { font-family: "Open Sans", Arial, sans-serif; color: var(--ink); position: relative; }
  .abs { position: absolute; }

  /* header */
  .brand { left: 75px; top: 36px; display: flex; align-items: center; gap: 10px; }
  .brand-dot { width: 40px; height: 40px; border-radius: 50%; background: var(--brand-blue); }
  .brand-name { font-weight: 700; color: var(--brand-gold); font-size: 22px; line-height: 22px; width: 230px; }
  .top-nav { left: 397px; top: 46px; display: flex; align-items: center; font-size: 13.5px; color: var(--ink-soft); }
  .top-nav a { display: flex; align-items: center; gap: 8px; color: inherit; text-decoration: none; }
  .top-nav .sep { width: 1px; height: 24px; background: var(--line); margin: 0 18px; }
  .user { right: 75px; top: 38px; display: flex; align-items: center; gap: 5px; font-size: 13.5px; color: var(--ink-soft); }
  .power { width: 41px; height: 41px; border-radius: 50%; border: 1px solid var(--brand-blue); display: flex; align-items: center; justify-content: center; }

  /* sidebar */
  .sidebar { left: 75px; top: 118px; width: 241px; height: 572px; border: 1px solid var(--line); border-top: none; background: var(--panel-bg); }
  .back-tab { position: absolute; left: -1px; top: 0; width: 131px; height: 33px; background: var(--brand-blue); color: #fff; font-size: 11.5px; display: flex; align-items: center; padding-left: 18px; gap: 8px; clip-path: polygon(0 0, 100% 0, 95% 100%, 0 100%); }
  .sidebar-topline { position: absolute; left: -1px; top: 0; width: 241px; height: 3px; background: var(--brand-blue); }
  .nav-list { position: absolute; top: 33px; left: 0; right: 0; list-style: none; }
  .nav-item { height: 72px; display: flex; align-items: center; gap: 12px; padding-left: 18px; border-top: 1px solid var(--line); font-size: 11.5px; font-weight: 700; color: #2f2f2f; letter-spacing: .2px; }
  .nav-item:first-child { border-top: none; }
  .nav-item.alt { background: var(--row-alt); }
  .nav-item.tall { height: 80px; }

  /* main panel */
  .panel { left: 338px; top: 118px; width: 787px; height: 572px; border: 1px solid var(--line); background: var(--panel-bg); }
  .scroll-track { position: absolute; right: 0; top: 0; width: 7px; height: 100%; background: var(--scroll-track); }
  .scroll-thumb { position: absolute; right: 1px; top: 135px; width: 5px; height: 38px; border-radius: 3px; background: var(--scroll-thumb); }
  .notice { left: 31px; top: 27px; display: flex; align-items: baseline; gap: 10px; }
  .notice-label { color: var(--brand-blue); font-size: 12.5px; }
  .notice-title { font-size: 11px; color: var(--ink); }
  .terms { left: 29px; top: 57px; width: 730px; font-size: 9.6px; line-height: 19.6px; color: var(--ink-soft); }
  .terms p + p { margin-top: 8px; }
  .emp-label { left: 29px; top: 200px; font-size: 11px; text-decoration: underline; color: var(--ink); }
  .emp-sub { left: 29px; top: 222px; font-size: 10px; color: var(--ink-soft); }
  .field { border: 1px solid var(--line); background: #fff; font-size: 10px; color: var(--ink-soft); padding: 10px 11px; }
  .sign-label { left: 590px; top: 332px; font-size: 10px; color: var(--ink-soft); }
  .btn-accept { left: 195px; top: 367px; width: 96px; height: 26px; background: var(--brand-blue); color: #fff; font-size: 10px; display: flex; align-items: center; justify-content: center; border: none; }
  .manager-title { left: 31px; top: 435px; font-size: 12.5px; color: var(--brand-blue); letter-spacing: .1px; }

  /* footer */
  .footer { left: 0; top: 732px; width: 1200px; height: 94px; background: var(--footer-bg); }
  .footer-dot { left: 80px; top: 24px; width: 42px; height: 42px; border-radius: 50%; background: var(--brand-blue); }
  .footer-links { left: 134px; top: 30px; font-size: 9.5px; color: var(--ink-soft); display: flex; gap: 8px; }
  .footer-links span.bar { color: var(--ink-muted); }
  .copyright { left: 134px; top: 57px; font-size: 9.5px; color: var(--ink-soft); }
  .social { left: 899px; top: 43px; display: flex; align-items: center; gap: 14px; font-size: 9.5px; color: var(--ink-soft); }
  .social-dot { width: 11px; height: 11px; border-radius: 50%; background: #666; }
  .code { left: 1162px; top: 44px; font-size: 10px; color: var(--ink-soft); }
</style>
</head>
<body>

<header>
  <div class="abs brand">
    <span class="brand-dot"></span>
    <span class="brand-name">SENTINEL WATCH SERVICES</span>
  </div>
  <nav class="abs top-nav">
    <a href="#"><svg width="15" height="13" viewBox="0 0 15 13"><path d="M7.5 1 L14 6.5 H12 V12 H9 V8 H6 V12 H3 V6.5 H1 Z" fill="#555"/></svg>Home</a>
    <span class="sep"></span>
    <a href="#"><svg width="14" height="14" viewBox="0 0 14 14"><circle cx="7" cy="7" r="7" fill="#555"/><text x="7" y="10.5" font-size="10" font-weight="700" text-anchor="middle" fill="#fff" font-family="Open Sans, sans-serif">?</text></svg>Help</a>
  </nav>
  <div class="abs user">
    <span>Dana Morel</span>
    <span class="power"><svg width="18" height="18" viewBox="0 0 18 18" fill="none" stroke="#1f5fa8" stroke-width="2.2" stroke-linecap="round"><path d="M5.2 4.5 A6.5 6.5 0 1 0 12.8 4.5"/><path d="M9 2 V9"/></svg></span>
  </div>
</header>

<aside class="abs sidebar">
  <div class="sidebar-topline"></div>
  <div class="back-tab"><span>«</span>Back To Profile</div>
  <ul class="nav-list">
    <li class="nav-item"><svg width="52" height="58" viewBox="0 0 52 58"><path d="M26 3 L48 10 V30 C48 44 38 52 26 56 C14 52 4 44 4 30 V10 Z" fill="#fff" stroke="#cfcfcf" stroke-width="2"/><ellipse cx="26" cy="30" rx="9" ry="7" fill="none" stroke="#f2b321" stroke-width="1.4"/><circle cx="26" cy="21" r="2.5" fill="none" stroke="#f2b321" stroke-width="1.4"/></svg>DIRECT DEPOSIT</li>
    <li class="nav-item alt"><svg width="52" height="58" viewBox="0 0 52 58"><path d="M26 3 L48 10 V30 C48 44 38 52 26 56 C14 52 4 44 4 30 V10 Z" fill="#fff" stroke="#cfcfcf" stroke-width="2"/><circle cx="26" cy="25" r="8" fill="none" stroke="#f2b321" stroke-width="1.4"/><path d="M21 31 L19 42 L26 38 L33 42 L31 31" fill="none" stroke="#f2b321" stroke-width="1.4"/></svg>CHANGE W-4</li>
    <li class="nav-item"><svg width="52" height="58" viewBox="0 0 52 58"><path d="M26 3 L48 10 V30 C48 44 38 52 26 56 C14 52 4 44 4 30 V10 Z" fill="#fff" stroke="#cfcfcf" stroke-width="2"/><circle cx="26" cy="25" r="6" fill="none" stroke="#f2b321" stroke-width="1.4"/><path d="M16 40 C16 33 36 33 36 40 Z" fill="none" stroke="#f2b321" stroke-width="1.4"/></svg>LABOUR CODE</li>
    <li class="nav-item alt tall"><svg width="52" height="58" viewBox="0 0 52 58"><path d="M26 3 L48 10 V30 C48 44 38 52 26 56 C14 52 4 44 4 30 V10 Z" fill="#fff" stroke="#cfcfcf" stroke-width="2"/><circle cx="26" cy="23" r="1.8" fill="#f2b321"/><path d="M26 27 V36 M19 22 C16 26 16 32 19 36 M33 22 C36 26 36 32 33 36" fill="none" stroke="#f2b321" stroke-width="1.6"/></svg>PERSONAL INFORMATION</li>
    <li class="nav-item tall"><svg width="52" height="58" viewBox="0 0 52 58"><path d="M26 3 L48 10 V30 C48 44 38 52 26 56 C14 52 4 44 4 30 V10 Z" fill="#fff" stroke="#cfcfcf" stroke-width="2"/><path d="M17 20 H35 V32 H24 L19 36 V32 H17 Z M21 25 H31 M21 28 H29" fill="none" stroke="#f2b321" stroke-width="1.4"/></svg>APPRAISAL AND REVIEW</li>
    <li class="nav-item alt tall"><svg width="52" height="58" viewBox="0 0 52 58"><path d="M26 3 L48 10 V30 C48 44 38 52 26 56 C14 52 4 44 4 30 V10 Z" fill="#fff" stroke="#cfcfcf" stroke-width="2"/><rect x="18" y="20" width="16" height="16" fill="none" stroke="#f2b321" stroke-width="1.4"/><path d="M23 31 L33 19" stroke="#f2b321" stroke-width="1.4"/></svg>WRITE UP-SLIP</li>
    <li class="nav-item tall"><svg width="52" height="58" viewBox="0 0 52 58"><path d="M26 3 L48 10 V30 C48 44 38 52 26 56 C14 52 4 44 4 30 V10 Z" fill="#fff" stroke="#cfcfcf" stroke-width="2"/><path d="M15 33 L22 26 L29 31 L37 23" fill="none" stroke="#f2b321" stroke-width="1.4"/><g fill="#fff" stroke="#f2b321" stroke-width="1.4"><circle cx="15" cy="33" r="2"/><circle cx="22" cy="26" r="2"/><circle cx="29" cy="31" r="2"/><circle cx="37" cy="23" r="2"/></g></svg>EMPLOYEE PERFORMANCE</li>
  </ul>
</aside>

<main class="abs panel">
  <div class="scroll-track"></div>
  <div class="scroll-thumb"></div>

  <div class="abs notice"><span class="notice-label">IMPORTANT!</span><span class="notice-title">Please read and Sign before Completing and Submitting</span></div>
  <div class="abs terms">
    <p>I Hereby &nbsp;Authorize SENTINEL WATCH SERVICES to deposit any amount owed me, as instructed by my employer, by initiating credit entries to my account at the financial institution (hereinafter Bank) indicated on this form. Furthur, I authorize Bank to Accept and to credit entries indicated by SENTINEL WATCH SERVICES to my account In the even that SENTINEL WATCH SERVICES deposits Funds erroneously into my Account I authorize SENTINEL WATCH SERVICES to debit my account for an amount not to exceed the original amount of the erroneous credit</p>
    <p>This authorization is to remain in full force and effect untill SENTINEL WATCH SERVICES and Bank have received written notice from me of its termination in such time and in such manner as to afford SENTINEL WATCH SERVICES an Bank reasonable opportunity to act on it</p>
  </div>

  <div class="abs emp-label">Employee Name :</div>
  <div class="abs emp-sub">Employee Signature</div>
  <div class="abs field" style="left:30px;top:252px;width:382px;height:34px;"></div>
  <div class="abs field" style="left:30px;top:297px;width:382px;height:56px;"></div>
  <div class="abs sign-label">Sign Date :</div>
  <div class="abs field" style="left:644px;top:322px;width:112px;height:32px;"></div>
  <button class="abs btn-accept">Accept Document</button>

  <div class="abs manager-title">ONLY PAYROLL MANAGER SIGNS BELOW</div>
  <div class="abs field" style="left:30px;top:470px;width:358px;height:34px;">Company Name*</div>
  <div class="abs field" style="left:30px;top:512px;width:358px;height:34px;">Employee File Number*</div>
  <div class="abs field" style="left:399px;top:470px;width:358px;height:76px;">Comments*</div>
</main>

<footer class="abs footer">
  <span class="abs footer-dot"></span>
  <nav class="abs footer-links">
    <span>HOME</span><span class="bar">|</span><span>PERSONAL LICENSES</span><span class="bar">|</span><span>FORMS/REQUESTS</span><span class="bar">|</span><span>TEAM CONTACT</span><span class="bar">|</span><span>BENEFITS</span><span class="bar">|</span><span>TRAINING</span><span class="bar">|</span><span>EQUIPMENT</span><span class="bar">|</span><span>HELP</span>
  </nav>
  <div class="abs copyright">© 2016 . SENTINEL WATCH | ALLRIGHTS RESERVED.</div>
  <div class="abs social">
    <span>CONNECT WITH US :</span>
    <span class="social-dot" role="img" aria-label="Social link 1"></span>
    <span class="social-dot" role="img" aria-label="Social link 2"></span>
    <span class="social-dot" role="img" aria-label="Social link 3"></span>
    <span class="social-dot" role="img" aria-label="Social link 4"></span>
    <span class="social-dot" role="img" aria-label="Social link 5"></span>
  </div>
  <div class="abs code">C11</div>
</footer>

</body>
</html>
```